Marta's Dwellings website

We need a simple website for our property investment business in the UK. We basically need our contact details and brief description.We have the company logo already done (via ArtFlockly) so please use these:https://drive.google.com/drive/folders/1szJ3iRhelElZ40NIFT7w-c14MaY3Y_oV?usp=sharingYou could use some stock photos of UK houses for now.Let me know when to provide more detailed descriptions, etc

Coding

Coded - Design and coding required

Number of Pages Required

1 page

Colors

Designer to choose colors to be used in the design.

```html
<!DOCTYPE html>
<html lang="en">
<head>
<meta charset="utf-8">
<title>Marta's Dwellings</title>
<link href="https://fonts.googleapis.com/css2?family=Questrial&display=swap" rel="stylesheet">
<style>
  :root {
    --blue: #1a8fd1;
    --ink: #222;
    --text: #555;
    --muted: #777;
    --line: #d9d9d9;
    --footer: #232323;
    --white: #fff;
  }
  * { box-sizing: border-box; margin: 0; padding: 0; }
  html, body { width: 1200px; height: 3100px; overflow: hidden; }
  body { position: relative; background: var(--white); font-family: "Questrial", sans-serif; color: var(--text); }
  .abs { position: absolute; }

  /* header */
  .site-header { position: absolute; left: 0; top: 0; width: 1200px; height: 112px; background: var(--white); }
  .brand { position: absolute; left: 112px; top: 40px; display: flex; align-items: center; gap: 10px; }
  .brand-mark { width: 22px; height: 22px; background: var(--ink); }
  .brand-name { font-size: 14px; letter-spacing: 4px; color: var(--ink); text-transform: uppercase; }
  .main-nav a { position: absolute; top: 50px; font-size: 15px; color: #333; text-decoration: none; }
  .main-nav a.is-active { color: var(--blue); }

  /* hero */
  .hero { position: absolute; left: 0; top: 112px; width: 1200px; height: 718px; }
  .hero-title { position: absolute; left: 569px; top: 470px; font-size: 48px; color: var(--white); letter-spacing: 1px; text-shadow: 0 2px 4px rgba(0,0,0,.4); }
  .hero-sub { position: absolute; left: 569px; top: 540px; width: 500px; font-size: 17px; line-height: 28px; color: var(--white); }
  .hero-dots span { position: absolute; top: 656px; width: 11px; height: 11px; border-radius: 50%; background: var(--white); }
  .hero-dots span.is-active { background: var(--blue); }

  /* about */
  .about-kicker { left: 155px; top: 914px; font-size: 34px; color: var(--ink); font-weight: 400; }
  .about-title { left: 155px; top: 954px; font-size: 42px; color: var(--ink); font-weight: 400; }
  .about-copy { left: 155px; top: 1030px; width: 382px; font-size: 14px; line-height: 26.6px; text-align: justify; }
  .read-more { left: 157px; top: 1212px; font-size: 15px; color: var(--ink); }
  .about-photo { left: 607px; top: 912px; width: 458px; height: 508px; background: linear-gradient(180deg, #c9d9ea 0%, #e6ecf2 30%, #9a5b43 55%, #5f7a3f 85%, #6d6d6d 100%); }
  .feature-box { left: 155px; top: 1300px; width: 709px; height: 144px; background: var(--white); border: 1px solid var(--line); }
  .feature-box .divider { position: absolute; left: 355px; top: 18px; width: 1px; height: 108px; background: var(--line); }
  .feature { position: absolute; top: 24px; }
  .feature h3 { font-weight: 400; font-size: 22px; color: var(--ink); }
  .feature p { margin-top: 16px; font-size: 13.5px; line-height: 25px; color: var(--text); width: 210px; }

  /* section heads */
  .section-title { left: 0; width: 1200px; text-align: center; font-size: 36px; font-weight: 400; color: var(--ink); }
  .section-rule { left: 558px; width: 84px; height: 3px; background: var(--blue); }

  /* property cards */
  .card { top: 1607px; width: 310px; height: 385px; background: var(--white); box-shadow: 0 0 4px rgba(0,0,0,.25); text-align: center; }
  .card-photo { width: 100%; height: 233px; }
  .card h3 { margin-top: 24px; font-weight: 400; font-size: 22px; color: var(--ink); }
  .card .rule { width: 54px; height: 2px; background: var(--blue); margin: 14px auto 0; }
  .card p { margin-top: 14px; font-size: 12.5px; line-height: 26px; color: var(--text); padding: 0 20px; }

  /* testimonial */
  .testimonial { left: 0; top: 2047px; width: 1200px; height: 419px; background: linear-gradient(90deg, #2a2522 0%, #3b332e 40%, #2d2a27 100%); }
  .avatar { left: 188px; top: 2158px; width: 202px; height: 202px; border-radius: 50%; border: 3px solid var(--blue); background: radial-gradient(circle at 50% 45%, #d8a98a 0%, #8a5a3e 65%, #5b3b28 100%); }
  .quote-mark { font-size: 40px; color: var(--blue); line-height: 1; }
  .quote-text { left: 439px; top: 2176px; width: 590px; font-size: 13px; line-height: 28.2px; color: var(--white); }
  .quote-name { left: 439px; top: 2314px; font-size: 20px; color: var(--blue); }
  .quote-date { left: 439px; top: 2345px; font-size: 15px; color: var(--white); }

  /* contact */
  .map { left: 155px; top: 2632px; width: 441px; height: 322px; background: linear-gradient(135deg, #eef0f2 0%, #e3e6e9 50%, #eceee9 100%); }
  .contact-info { left: 638px; top: 2635px; width: 430px; font-size: 13.5px; line-height: 26px; color: #333; }
  .field { width: 178px; height: 42px; border: 1px solid var(--line); font-size: 12.5px; padding: 14px 16px; color: #555; }
  .field-message { left: 824px; top: 2739px; width: 221px; height: 142px; }
  .submit { left: 640px; top: 2901px; width: 125px; height: 43px; background: var(--blue); color: var(--white); font-size: 16px; letter-spacing: 1px; text-align: center; line-height: 43px; }

  .site-footer { left: 0; top: 3031px; width: 1200px; height: 69px; background: var(--footer); color: var(--white); text-align: center; font-size: 13px; line-height: 69px; }
</style>
</head>
<body>

<header class="site-header">
  <div class="brand"><span class="brand-mark"></span><span class="brand-name">Marta's Dwellings</span></div>
  <nav class="main-nav">
    <a class="is-active" style="left:542px">Home</a>
    <a style="left:628px">About Us</a>
    <a style="left:733px">Services</a>
    <a style="left:832px">Property</a>
    <a style="left:933px">News</a>
    <a style="left:1015px">Contact Us</a>
  </nav>
</header>

<section class="hero">
  <svg class="abs" style="left:0;top:0" width="1200" height="718" viewBox="0 0 1200 718">
    <defs>
      <linearGradient id="heroSky" x1="0" y1="0" x2="0" y2="1">
        <stop offset="0" stop-color="#8fb8e0"/>
        <stop offset="0.35" stop-color="#b86a4c"/>
        <stop offset="0.65" stop-color="#7a5345"/>
        <stop offset="1" stop-color="#4b4550"/>
      </linearGradient>
    </defs>
    <path d="M0 0 H1200 V588 L600 718 L0 588 Z" fill="url(#heroSky)" role="img" aria-label="Photo of red-brick detached houses on a suburban UK street"/>
    <path d="M0 588 L600 718 L1200 588 L1200 604 L600 714 L0 604 Z" fill="var(--white)"/>
    <path d="M0 588 L600 718 L1200 588 L1200 594 L600 718 L0 594 Z" fill="var(--blue)"/>
  </svg>
  <div class="hero-title">MARTA'S DWELLINGS</div>
  <div class="hero-sub">Sed ut perspiciatis unde omnis iste natus error sit voluptatem accusantium doloremque laudantium</div>
  <div class="hero-dots"><span style="left:577px"></span><span class="is-active" style="left:595px"></span><span style="left:613px"></span></div>
</section>

<section class="about">
  <h2 class="abs about-kicker">ABOUT</h2>
  <h2 class="abs about-title">MARTA'S DWELLINGS</h2>
  <p class="abs about-copy">Sed ut perspiciatis unde omnis iste natus error sit voluptatem accusantium doloremque laudantium, totam rem aperiam, eaque ipsa quae ab illo inventore veritatis et quasi architecto beatae vitae dicta sunt explicabo. Nemo enim ipsam volu ptatem quia voluptas sit aspernatur aut odit aut fugit, sed eos qui ratione voluptatem sequi nesciunt.</p>
  <div class="abs read-more">Read More &nbsp;&#187;</div>
  <div class="abs about-photo" role="img" aria-label="Photo of a terraced brick house row beside a tree-lined footpath"></div>
  <div class="abs feature-box">
    <div class="feature" style="left:20px">
      <svg width="72" height="82" viewBox="0 0 72 82" fill="none" stroke="var(--blue)" stroke-width="2.5">
        <path d="M6 80 V44 L30 20 L54 44 V80 Z"/><path d="M30 20 V4 L48 22"/><rect x="14" y="56" width="12" height="12"/><rect x="34" y="56" width="12" height="24"/>
      </svg>
    </div>
    <div class="feature" style="left:112px"><h3>Property</h3><p>Sed ut perspiciatis unde omnis iste accusant iu dolorem....</p></div>
    <div class="divider"></div>
    <div class="feature" style="left:388px">
      <svg width="76" height="80" viewBox="0 0 76 80" fill="none" stroke="var(--blue)" stroke-width="3">
        <circle cx="22" cy="40" r="19"/><circle cx="50" cy="26" r="16"/><circle cx="50" cy="58" r="19" fill="var(--blue)"/>
        <text x="22" y="48" font-size="22" text-anchor="middle" fill="var(--blue)" stroke="none" font-family="Questrial, sans-serif">$</text>
        <text x="50" y="33" font-size="18" text-anchor="middle" fill="var(--blue)" stroke="none" font-family="Questrial, sans-serif">$</text>
        <text x="50" y="66" font-size="22" text-anchor="middle" fill="var(--white)" stroke="none" font-family="Questrial, sans-serif">$</text>
      </svg>
    </div>
    <div class="feature" style="left:488px"><h3>Investment</h3><p>Sed ut perspiciatis unde omnis iste accusant iu dolorem....</p></div>
  </div>
</section>

<section class="properties">
  <h2 class="abs section-title" style="top:1512px">OUR PROPERTY</h2>
  <div class="abs section-rule" style="top:1570px"></div>
  <article class="abs card" style="left:112px">
    <div class="card-photo" role="img" aria-label="Photo of Victorian terraced houses behind hedges" style="background:linear-gradient(180deg,#e9e4dc 0%,#a48a78 45%,#4d5c3a 80%,#6b6b6b 100%)"></div>
    <h3>Property Name</h3><div class="rule"></div>
    <p>Sed ut perspiciatis unde omnis iste natus error voluptatem accusantium doloremque</p>
  </article>
  <article class="abs card" style="left:445px">
    <div class="card-photo" role="img" aria-label="Photo of an aerial view over rows of new-build houses" style="background:linear-gradient(180deg,#7fb0e0 0%,#c9d6de 40%,#8a6a55 65%,#5a4a42 100%)"></div>
    <h3>Property Name</h3><div class="rule"></div>
    <p>Sed ut perspiciatis unde omnis iste natus error voluptatem accusantium doloremque</p>
  </article>
  <article class="abs card" style="left:779px">
    <div class="card-photo" role="img" aria-label="Photo of a large red-brick apartment house under a blue sky" style="background:linear-gradient(180deg,#3f7fd0 0%,#9cc0e6 35%,#8a4a38 65%,#b9b2a8 100%)"></div>
    <h3>Property Name</h3><div class="rule"></div>
    <p>Sed ut perspiciatis unde omnis iste natus error voluptatem accusantium doloremque</p>
  </article>
</section>

<section class="abs testimonial" role="img" aria-label="Darkened photo of a brick terraced street">
  <svg class="abs" style="left:64px;top:155px" width="22" height="110" viewBox="0 0 22 110"><path d="M20 2 L2 55 L20 108" fill="none" stroke="var(--white)" stroke-width="1.5"/></svg>
  <svg class="abs" style="left:1122px;top:155px" width="22" height="110" viewBox="0 0 22 110"><path d="M2 2 L20 55 L2 108" fill="none" stroke="var(--white)" stroke-width="1.5"/></svg>
</section>
<div class="abs avatar" role="img" aria-label="Portrait photo of the client giving the testimonial"></div>
<div class="abs quote-mark" style="left:414px;top:2154px">&#8220;</div>
<p class="abs quote-text">Sed ut perspiciatis unde omnis iste natus error sit voluptatem accusantium doloremque laudantium, totam rem aperiam, eaque ipsa quae ab illo inventore veritatis et quasi architecto beatae vitae dicta sunt explic abo. Nemo enim ipsam voluptatem quia voluptas sit aspernatur aut odit aut fugit, sed quia consequuntur magni dolores eos qui ratione voluptatem sequi nesciunt.</p>
<div class="abs quote-mark" style="left:768px;top:2276px">&#8221;</div>
<div class="abs quote-name">-Clara Wendt</div>
<div class="abs quote-date">Posed on 13 may,2019</div>

<section class="contact">
  <h2 class="abs section-title" style="top:2514px">CONTACT US</h2>
  <div class="abs section-rule" style="top:2570px"></div>
  <div class="abs map" role="img" aria-label="Street map showing the office location">
    <svg class="abs" style="left:232px;top:136px" width="16" height="22" viewBox="0 0 16 22"><path d="M8 21 C3 13 1 10 1 7 A7 7 0 0 1 15 7 C15 10 13 13 8 21 Z" fill="#e53935"/><circle cx="8" cy="7" r="2.5" fill="#8b1a1a"/></svg>
  </div>
  <div class="abs contact-info">
    <p>Address : # Unit 5, Brookfield Court, 14-16 Alder Row, Kettlebrook, Westmarsh, United Kingdom, WM4 7QD</p>
    <p style="margin-top:9px">Phone : 000-555-0187 &nbsp;- &nbsp;Email : hello@martasdwellings-example.com</p>
  </div>
  <div class="abs field" style="left:640px;top:2739px">Name :</div>
  <div class="abs field" style="left:640px;top:2790px">Email :</div>
  <div class="abs field" style="left:640px;top:2839px">Phone :</div>
  <div class="abs field field-message">Message :</div>
  <div class="abs submit">SUBMIT</div>
</section>

<footer class="abs site-footer">&copy; Copyright-2019 Marta's Dwellings. All rights reserved.</footer>

</body>
</html>
```